Need a Zine cover designed

I’m looking for someone who can design an eye catching and original zine cover. Incorporating the logo I included below. I’m not 100% sure which logo I want to use on the cover, if it’s possible to see how you incorporate the logos on a sample will make it easier for me to decide. Thank you for your time.
For the second logo I’m unsure how to remove the grey background, but I do not want it included in the zine cover
The title of the zine is:
Marigold Crossing
perspectives of culture, life, & love

```html
<!DOCTYPE html>
<html lang="en">
<head>
<meta charset="utf-8">
<title>Marigold Crossing — Zine Cover</title>
<link rel="stylesheet" href="https://fonts.googleapis.com/css2?family=Bungee&family=Yellowtail&display=swap">
<style>
  :root {
    --backdrop: #a3a4a6;
    --paper-light: #dcb9a6;
    --paper-mid: #cfa792;
    --paper-dark: #b98f7b;
    --fold: rgba(120, 80, 62, 0.35);
    --fold-light: rgba(255, 240, 230, 0.45);
    --ink-red: #c3161b;
  }
  html, body {
    margin: 0;
    padding: 0;
    width: 1176px;
    height: 1200px;
    overflow: hidden;
    background: var(--backdrop);
  }
  .canvas {
    position: relative;
    width: 1176px;
    height: 1200px;
  }
  .cover {
    position: absolute;
    left: 198px;
    top: 50px;
    width: 780px;
    height: 1100px;
    overflow: hidden;
    box-shadow: 0 10px 30px rgba(0,0,0,0.18);
  }
  .cover__paper {
    position: absolute;
    inset: 0;
    background:
      radial-gradient(ellipse at 30% 20%, var(--paper-light) 0%, transparent 60%),
      radial-gradient(ellipse at 75% 80%, var(--paper-light) 0%, transparent 55%),
      linear-gradient(160deg, var(--paper-mid) 0%, var(--paper-light) 45%, var(--paper-mid) 100%);
  }
  .cover__folds {
    position: absolute;
    inset: 0;
  }
  .cover__brand {
    position: absolute;
    left: 170px;
    top: 215px;
    margin: 0;
    font-family: "Bungee", sans-serif;
    font-size: 34px;
    line-height: 1;
    color: var(--ink-red);
    display: flex;
    align-items: center;
    gap: 12px;
  }
  .cover__brand-dot {
    width: 18px;
    height: 18px;
    border-radius: 50%;
    background: var(--ink-red);
  }
  .cover__title {
    position: absolute;
    left: 0;
    right: 0;
    top: 440px;
    margin: 0;
    text-align: center;
    font-family: "Bungee", sans-serif;
    font-weight: 400;
    font-size: 104px;
    line-height: 1.02;
    color: var(--ink-red);
    letter-spacing: -1px;
  }
  .cover__title-line { display: block; }
  .cover__tagline {
    position: absolute;
    left: 200px;
    top: 850px;
    margin: 0;
    font-family: "Yellowtail", cursive;
    color: var(--ink-red);
    transform: rotate(-9deg);
    transform-origin: left center;
    line-height: 1.05;
  }
  .cover__tagline-top {
    display: block;
    font-size: 56px;
    padding-left: 20px;
  }
  .cover__tagline-bottom {
    display: block;
    font-size: 88px;
  }
</style>
</head>
<body>
<main class="canvas">
  <article class="cover">
    <div class="cover__paper" role="img" aria-label="Creased pinkish kraft paper covered in faint pencil scribbles"></div>
    <svg class="cover__folds" width="780" height="1100" viewBox="0 0 780 1100" aria-hidden="true">
      <line x1="0" y1="300" x2="780" y2="280" stroke="var(--fold)" stroke-width="2"/>
      <line x1="0" y1="302" x2="780" y2="282" stroke="var(--fold-light)" stroke-width="2"/>
      <line x1="0" y1="560" x2="780" y2="545" stroke="var(--fold)" stroke-width="2"/>
      <line x1="0" y1="562" x2="780" y2="547" stroke="var(--fold-light)" stroke-width="2"/>
      <line x1="0" y1="815" x2="780" y2="800" stroke="var(--fold)" stroke-width="2"/>
      <line x1="0" y1="817" x2="780" y2="802" stroke="var(--fold-light)" stroke-width="2"/>
      <line x1="26" y1="0" x2="26" y2="1100" stroke="var(--fold)" stroke-width="1.5"/>
    </svg>
    <p class="cover__brand"><span class="cover__brand-dot"></span>Sunroom Society</p>
    <h1 class="cover__title">
      <span class="cover__title-line">Marigold</span>
      <span class="cover__title-line">Crossing</span>
    </h1>
    <p class="cover__tagline">
      <span class="cover__tagline-top">Perspective Of Life</span>
      <span class="cover__tagline-bottom">Culture &amp; Love</span>
    </p>
  </article>
</main>
</body>
</html>
```